Wine Bottle Label for Tall Fern Wines

We are a small, newly established winery in need of an original, bold and outstanding bottle label design for our Tall Fern wine.

Our vineyard and winery are located on a 200 acre farm in a remote part of southern Oregon. The name "Tall Fern" was inspired by the large, overgrown size of all of the foliage here, including our grapevines. Things grow large and vigorous in Oregon! And everything is very lush and green. It is almost surreal or other-worldly, like the landscapes seen in the Keeper of The Stones movies, or the land of Quill. It is a place that makes you say "wow" with its epic, large scale, natural beauty.

The name "Tall Fern" also captures the essence of our wine. It is big in flavor, quality and color. Our first release is a Pinot Noir (red). Pinot Noir wines often are subtle in flavor and thin in their color. Our label should convey that our Pinot Noir is a much more robust, darker, heavier, meatier, more flavorful wine that is a lot more fun than an "ordinary" wine. At the same time, this wine is not cheap, and so nothing in the label should convey "bargain," "low price," or "cheapness." This is a fine wine with a sense of adventure. Be sure to convey "quality" with your design along with "big," "adventure" and "fun".

The label should appeal to a younger demographic, both male and female, between the ages of 21 and 35. It should be non-traditional and adventurous and suggest a pushing of boundaries and a breaking of rules. This Pinot Noir does not conform to the normal "limitations" of the variety, therefore the label should not conform. It should have an "organic" or "natural" or "agricultural" vibe, as opposed to something mechanical or technical. It should, however, be contemporary. Do not confuse "natural" or "organic" with being nostalgic or old school. Think "agri-hipsters."

The label should be designed to fit on a Burgundy-style wine bottle (photo attached for reference). (Note: All Pinot Noir and Chardonnay is bottled in Burgundy bottles, If you are not sure about the bottle shape you can go to a local store and compare the various bottles. Locate a bottle of Pinot Noir or Chardonnay or anything identified as a "Burgundy Wine," and it should be the correct bottle. The tall, skinny bottles used for Cabernet Sauvignon are NOT correct)). Please see the "Must Have" notes for more on the bottle.

In summary, the final project should be a wine bottle label design that conveys bigness, vastness, adventurous, non-traditional, high quality wine. A good tagline to keep in mind is "Living Large."

Target Market(s)

Young, hip, non-conformist wine drinkers aged 21-35 with a sense of adventure and an appreciation of quality.

Industry/Entity Type

School

Requirements
Must have
• *Must contain the words:

Tall Fern (the brand)
2013 Pinot Noir (the vintage year and variety)

*The label must be designed to fit a Burgundy-style wine bottle. A photo is attached for reference.

*Additionally, the label needs to fit on the lower, widest part of the bottle. The label will be printed on sticky paper and rolled onto the bottle with a machine. The machine cannot apply labels to the neck of the bottle. The maximum size of a label that will fit this space is 5.5 inches wide by 4.5 inches tall. You DO NOT have to fill ALL of this space or confine the label shape to a rectangle, but the label cannot exceed this size or it won't stick to the bottle properly. It will really help if you can put your hands on an actual bottle to see the logistics of applying the label. But if that is not possible, just do your best with the instructions you have. I am confident the winning design could be adjusted to fit the bottle, if necessary
Nice to have
• *Wine grape leaf or leaves.

*A concept I have been playing with is sunlight shining through leaves like light through a Marlowe lamp or a stained glass window. This is NOT a requirement for this label. However, if the concept inspires and idea, I would be most happy to see it.
Should not have
• IF a leaf or leaves are included in the design (not a requirement) they MUST be wine grapevine leafs and preferably leaves of the Pinot Noir vine. Do not use generic leaves or identifiable leaves such as oak leaves, maple leaves, or anything that looks like the Canadian flag or the Halden Ridge Ravens hockey logo. Reference the attached photos of wine grape leaves to see the correct leaf type. I am happy to email more photos upon request. These photos may be used in whole or in part in your design, however, a leaf from a photo is NOT a requirement, nor is the image of a leaf or leaves.

This label should NOT be designed for Bordeaux-style wine bottles (the tall, skinny ones).

```html
<!DOCTYPE html>
<html lang="en">
<head>
<meta charset="utf-8">
<title>Tall Fern Pinot Noir 2013 – Bottle Label</title>
<link rel="stylesheet" href="https://fonts.googleapis.com/css2?family=Pinyon+Script&family=Cormorant+Garamond:wght@600&family=Roboto:wght@400&display=swap">
<style>
  :root {
    --canvas: #ffffff;
    --label-black: #0e0e0f;
    --label-edge: #1e1e20;
    --grape-light: #8a63b8;
    --grape-mid: #4d2f78;
    --grape-deep: #1c1030;
    --gold: #c9b98a;
    --gold-bright: #efe3b8;
    --gold-line: #a8915a;
    --vintage-white: #e9e6df;
    --fine-print: #b8b8b8;
  }
  * { margin: 0; padding: 0; box-sizing: border-box; }
  html, body {
    width: 1200px;
    height: 900px;
    overflow: hidden;
    background: var(--canvas);
  }
  .label {
    position: absolute;
    left: 320px;
    top: 100px;
    width: 560px;
    height: 700px;
    filter: drop-shadow(0 2px 6px rgba(0,0,0,0.35));
  }
  .label-shape {
    position: absolute;
    inset: 0;
    width: 560px;
    height: 700px;
  }
  .label-text {
    position: absolute;
    left: 0;
    width: 100%;
    text-align: center;
    line-height: 1;
  }
  .brand-name {
    top: 150px;
    font-family: "Pinyon Script", cursive;
    font-size: 96px;
    color: var(--gold-bright);
    text-shadow: 0 1px 0 #6e5d33, 0 2px 3px rgba(0,0,0,0.6);
  }
  .variety {
    top: 338px;
    font-family: "Cormorant Garamond", serif;
    font-weight: 600;
    font-size: 48px;
    color: var(--gold);
    text-shadow: 0 2px 3px rgba(0,0,0,0.6);
  }
  .vintage-row {
    position: absolute;
    top: 462px;
    left: 10px;
    width: 540px;
    display: flex;
    align-items: center;
    gap: 18px;
  }
  .vintage-rule {
    flex: 1;
    height: 2px;
    background: linear-gradient(90deg, var(--gold-line), var(--gold-bright), var(--gold-line));
  }
  .vintage {
    font-family: "Cormorant Garamond", serif;
    font-weight: 600;
    font-size: 40px;
    color: var(--vintage-white);
    line-height: 1;
  }
  .origin {
    top: 524px;
    font-family: "Pinyon Script", cursive;
    font-size: 38px;
    line-height: 46px;
    color: var(--gold);
  }
  .fine-print {
    position: absolute;
    top: 664px;
    left: 10px;
    right: 14px;
    display: flex;
    justify-content: space-between;
    font-family: "Roboto", sans-serif;
    font-size: 16px;
    color: var(--fine-print);
    letter-spacing: 0.3px;
  }
</style>
</head>
<body>
  <main class="label">
    <svg class="label-shape" viewBox="0 0 560 700" aria-hidden="false">
      <defs>
        <clipPath id="label-outline">
          <path d="M0,96 C0,70 20,62 40,66 C44,38 70,28 92,40 C100,14 130,4 156,18 C168,2 196,0 212,14 C228,0 256,4 266,22 C282,8 312,10 322,30 C338,18 366,22 376,42 C392,30 420,36 428,56 C446,48 470,56 474,76 C492,68 520,78 524,100 C540,98 556,106 560,120 L560,690 Q560,700 550,700 L10,700 Q0,700 0,690 Z"/>
        </clipPath>
        <radialGradient id="grape-tones" cx="55%" cy="35%" r="75%">
          <stop offset="0" stop-color="var(--grape-light)"/>
          <stop offset="0.5" stop-color="var(--grape-mid)"/>
          <stop offset="1" stop-color="var(--grape-deep)"/>
        </radialGradient>
        <linearGradient id="grape-fade" x1="0" y1="0" x2="0" y2="1">
          <stop offset="0.75" stop-color="#000" stop-opacity="0"/>
          <stop offset="1" stop-color="#000" stop-opacity="0.55"/>
        </linearGradient>
      </defs>
      <g clip-path="url(#label-outline)">
        <rect class="label-body" x="0" y="0" width="560" height="700" fill="var(--label-black)"/>
        <g class="grape-photo" role="img" aria-label="Photograph of a dark purple Pinot Noir grape cluster">
          <rect x="0" y="0" width="560" height="404" fill="url(#grape-tones)"/>
          <rect x="0" y="0" width="560" height="404" fill="url(#grape-fade)"/>
        </g>
      </g>
      <path d="M0,96 C0,70 20,62 40,66 C44,38 70,28 92,40 C100,14 130,4 156,18 C168,2 196,0 212,14 C228,0 256,4 266,22 C282,8 312,10 322,30 C338,18 366,22 376,42 C392,30 420,36 428,56 C446,48 470,56 474,76 C492,68 520,78 524,100 C540,98 556,106 560,120 L560,690 Q560,700 550,700 L10,700 Q0,700 0,690 Z" fill="none" stroke="var(--label-edge)" stroke-width="3"/>
    </svg>

    <h1 class="label-text brand-name">Tall Fern</h1>
    <p class="label-text variety">Pinot Noir</p>
    <div class="vintage-row">
      <span class="vintage-rule"></span>
      <span class="vintage">2013</span>
      <span class="vintage-rule"></span>
    </div>
    <p class="label-text origin">Product of<br>Southern Oregon</p>
    <div class="fine-print">
      <span class="alcohol">ALCOHOL 13.5% BY VOLUME</span>
      <span class="volume">750ML</span>
    </div>
  </main>
</body>
</html>
```